Cat-products company needs smart, yet endearing, business card

We need a business card design for a new, but up-and-running, business based in Honolulu, Hawaii. The business is Purrnest Nook Co. Our first product is the most environmentally-friendly cat grass kit ever seen on the planet. Future products, currently in the R&D phase, will include a variety of exciting cat scratchers. We also do consulting work to help apartment-dwellers make their home more cat-friendly and, in the future, plan on doing full, custom installs of structure to create high walkways for cats.

Target Market(s)

Middle-aged, apartment-dwelling, middle-class workers who own 1 or more cats and who dote on them.

Industry/Entity Type

Pet Care

Contact Information for Business Card

A striking, professional, yet warm and friendly design is what we're after.

Font styles to use
Serif
Sans Serif
Other font styles liked:
• Comfortaa

Colors

Designer to choose colors to be used in the design.

Requirements
Must have
• The company logo: (see attachment)
• The company name: Purrnest Nook Co
• The web address: www.purrnestnookco.com
• Email: support@purrnestnookco.com
• Phone: +1 (808) 571 6023
• Update (Fri Jun 30 3017 7:45pm Hawaii Time) I would like, is possible, uploaded picture of the cat grass kit on the back of the card with some text along the lines of: Purrnest Nook Co - Maker Of The Leafiest Feline Sprout Set Yet
Nice to have
• A cat picture, cartoon, real or silhouette that illustrates cats in action and/or relaxing; ie using the apartment space to live, play and relax in and being well-contented.
• Most of the website is done in the font: Comfortaa. It might be nice to continue using this for brand consistency.
Should not have
• Hard-to-read fonts.

```html
<!DOCTYPE html>
<html lang="en">
<head>
<meta charset="utf-8">
<title>Purrnest Nook Co – Business Card</title>
<link rel="stylesheet" href="https://fonts.googleapis.com/css2?family=Comfortaa:wght@700&family=Questrial&display=swap">
<style>
  :root {
    --backdrop: #2b2b2b;
    --card: #f3f3f2;
    --brown: #55312a;
    --gold: #f0a91b;
    --ink: #4a4a4a;
    --light: #ffffff;
    --dot: #8a6a60;
  }
  * { margin: 0; padding: 0; box-sizing: border-box; }
  html, body { width: 1200px; height: 960px; overflow: hidden; }
  body {
    position: relative;
    background: var(--backdrop);
    font-family: "Questrial", "Century Gothic", sans-serif;
  }
  .card {
    position: absolute;
    width: 600px;
    height: 342px;
    background: var(--card);
    border-radius: 22px;
    overflow: hidden;
  }
  .card--front { left: 314px; top: 113px; }
  .card--back { left: 311px; top: 472px; }

  .brand-name {
    font-family: "Comfortaa", sans-serif;
    font-weight: 700;
    color: var(--brown);
    text-align: center;
    position: absolute;
    left: 0; right: 0;
  }
  .card--front .brand-name { top: 70px; font-size: 46px; line-height: 1.1; }

  .info-band {
    position: absolute;
    left: 0; right: 0;
    top: 217px;
    height: 90px;
    background: var(--brown);
  }
  .holder {
    position: absolute;
    left: 36px;
    top: 22px;
  }
  .holder-name {
    font-family: "Comfortaa", sans-serif;
    font-weight: 700;
    font-size: 20px;
    color: var(--gold);
    text-transform: uppercase;
    letter-spacing: 0.5px;
  }
  .holder-role {
    font-size: 15px;
    color: var(--light);
    margin-top: 4px;
    letter-spacing: 0.5px;
  }
  .contact {
    position: absolute;
    right: 25px;
    top: 16px;
    list-style: none;
    text-align: right;
    color: var(--light);
    font-size: 14.5px;
    line-height: 19px;
  }
  .address {
    position: absolute;
    left: 0; right: 0;
    top: 316px;
    text-align: center;
    font-size: 13.5px;
    color: var(--ink);
  }

  .social {
    position: absolute;
    right: 16px;
    top: 19px;
    display: flex;
    gap: 2px;
  }
  .social span {
    width: 22px; height: 22px;
    border-radius: 50%;
    background: var(--dot);
  }
  .brand-dot {
    position: absolute;
    left: 270px;
    top: 82px;
    width: 60px; height: 60px;
    border-radius: 50%;
    background: var(--gold);
  }
  .card--back .brand-name { top: 175px; font-size: 44px; }
  .web {
    position: absolute;
    left: 0; right: 0;
    top: 294px;
    text-align: center;
    font-size: 15px;
    letter-spacing: 5px;
    color: var(--ink);
  }
</style>
</head>
<body>
  <section class="card card--front">
    <h1 class="brand-name">Purrnest Nook Co</h1>
    <div class="info-band">
      <div class="holder">
        <p class="holder-name">Leilani Kahale</p>
        <p class="holder-role">CEO/FOUNDER</p>
      </div>
      <ul class="contact">
        <li>+1 (808) 571 6023</li>
        <li>support@purrnestnookco.com</li>
        <li>www.purrnestnookco.com</li>
      </ul>
    </div>
    <p class="address">4128 Hibiscus Lane, Honolulu, Hawaii 96815</p>
  </section>

  <section class="card card--back">
    <div class="social" aria-label="Social links">
      <span></span><span></span><span></span><span></span>
    </div>
    <div class="brand-dot"></div>
    <h2 class="brand-name">Purrnest Nook Co</h2>
    <p class="web">www.purrnestnookco.com</p>
  </section>
</body>
</html>
```